Migration and redesign of existing website to WordPress using DIVI 3

I. TASK OBJECTIVE:
- Redesign our existing website www.kelvaleheelcare.com.au with a fresh new look and migrate to new Wordpress site based on DIVI3 theme. The site will contain the same basic functionality as the existing site (with some small changes).

II. STYLE/ DESIGN ASPECT:
As an example of a site that I like the look of, see https://pebblequarn.com/. I like the use of shadows, and this would go well with the little animations you can do with Divi (e.g. when hovering over pics).

1. What I am looking for is a design which has lots of white space, is modern and friendly looking (but still not too cute or frivolous, as we are a medical practice)
2. DESIGN that is NOT TOO rectangular or blocky.
3. Please take into consideration our Users are Older market, so any icons or navigation features need to be very easy to understand and not too small.
4. Must be easy to navigate
5. We are are happy to go with a new colour scheme, and are working on some ideas for this, but happy to take suggestions.

III. SPECIFICATIONS:
1. 5+ Pages (should flow like the current site)
2. Using Wordpress Divi 3 theme.
3. I'd like every page to have a "book now" button and a contact form in a sidebar so that users can click the button or fill in the contact form without scrolling at all. EXCEPT ON THE HOME PAGE, where there should still be a book now button (maybe on the top right in the header of all pages?), and maybe a contact us button which scrolls down to the contact area at the bottom of the HOME page. I don't think a side bar is necessarily required on the home page, but if you think it makes sense from a design perspective please let me know.
4. AT THE BOTTOM OF THE PAGE, just above the FOOTER, I'd like a row of trust logos for various organisations that we are affiliated with. (A list of this company will be provided later but you could temporarily use placeholders)

Once we have a structure in place, we can migrate most of the content. Please let me know if I'm not being clear or you need further information.

Podiatry Customers and Referrors

Health Care

5+ page

• Simple to navigate.
• Contact/booking details on most if not all pages - please see specification above
• Section for Trusted Affiliates above the footer
• Wordpress using Divi3 Theme
• Not too busy with the design. Plenty of white space or light background.
• Should not be complicated to navigate.
• TOO rectangular or blocky designs

```html
<!DOCTYPE html>
<html lang="en">
<head>
<meta charset="utf-8">
<title>Kelvale Heel Care</title>
<link href="https://fonts.googleapis.com/css2?family=Open+Sans:wght@300;400;600;700&family=Raleway:wght@300;400;500;600&display=swap" rel="stylesheet">
<style>
:root{
  --teal:#1c8c92;
  --teal-dark:#0e6870;
  --teal-light:#2fb0b2;
  --ink:#3a3f44;
  --muted:#6e767c;
  --line:#dfe4e6;
  --white:#ffffff;
  --soft:#f4f7f8;
  --badge:#d5dcdf;
}
*{box-sizing:border-box;margin:0;padding:0}
html,body{width:1200px;height:3048px;overflow:hidden}
body{font-family:"Open Sans",Arial,sans-serif;color:var(--ink);background:var(--white);position:relative}
section,header,footer{position:absolute;left:0;width:1200px}
h2{font-family:"Raleway",Arial,sans-serif;font-weight:400;font-size:34px;text-align:center;color:var(--ink)}
.rule{width:60px;height:2px;background:var(--teal);margin:14px auto 0}
.btn{display:inline-block;border:1px solid var(--teal);color:var(--teal);font-size:13px;padding:9px 20px;border-radius:3px;background:var(--white);box-shadow:0 2px 5px rgba(0,0,0,.12)}
.btn-light{border-color:var(--white);color:var(--white);background:transparent}

/* header */
.site-header{top:0;height:100px;background:var(--white);box-shadow:0 2px 8px rgba(0,0,0,.08);z-index:5}
.brand{position:absolute;left:40px;top:28px;display:flex;align-items:center;gap:12px}
.brand-dot{width:44px;height:44px;border-radius:50%;background:var(--teal)}
.brand-name{font-family:"Raleway",sans-serif;font-weight:600;font-size:22px;color:var(--teal-dark)}
.search{position:absolute;left:560px;top:14px;width:220px;height:28px;border:1px solid var(--line);border-radius:14px;font-size:12px;color:var(--muted);padding:6px 14px}
.book-now{position:absolute;left:800px;top:12px;height:32px;padding:0 18px;line-height:32px;border-radius:16px;background:var(--teal);color:var(--white);font-size:13px;font-weight:600;box-shadow:0 2px 5px rgba(0,0,0,.15)}
.phone{position:absolute;right:40px;top:12px;display:flex;align-items:center;gap:10px;color:var(--teal-dark)}
.phone small{display:block;font-size:11px;color:var(--muted)}
.phone strong{font-size:17px;font-weight:600}
.main-nav{position:absolute;right:40px;top:64px;display:flex;gap:24px;font-size:14px}
.main-nav a{color:var(--ink);text-decoration:none}
.main-nav a.current{color:var(--teal)}

/* hero */
.hero{top:100px;height:560px;overflow:hidden}
.hero-photo{position:absolute;inset:0;background:linear-gradient(110deg,#5d5f62 0%,#9fa3a6 38%,#b9bcbe 62%,#cfd1d1 100%)}
.hero-shade{position:absolute;inset:0;background:linear-gradient(270deg,rgba(14,50,56,.62) 0%,rgba(14,50,56,.35) 35%,rgba(14,50,56,0) 60%)}
.hero-title{position:absolute;right:50px;top:70px;color:var(--white);font-family:"Raleway",sans-serif;font-weight:300;text-shadow:0 2px 8px rgba(0,0,0,.45)}
.hero-title .l1{font-size:62px;display:block;text-align:right}
.hero-title .l2{font-size:40px;display:block;line-height:1.2}
.hero-title b{font-weight:600}
.arrow{position:absolute;top:230px;width:40px;height:60px;background:rgba(0,0,0,.25)}
.arrow.left{left:0}.arrow.right{right:0}
.hero-wave{position:absolute;bottom:-1px;left:0}

/* practice areas */
.practice{top:700px;height:420px}
.cards{display:flex;justify-content:center;gap:32px;margin-top:40px}
.card{width:220px;display:flex;flex-direction:column;height:300px}
.card-img{height:130px;border-radius:4px;box-shadow:0 4px 10px rgba(0,0,0,.15)}
.card h3{font-family:"Raleway",sans-serif;font-weight:600;font-size:16px;color:var(--teal);margin:16px 0 8px}
.card p{font-size:12px;line-height:1.6;color:var(--muted);margin-bottom:14px;flex:1}
.card .btn{align-self:flex-start}

/* relief band */
.relief{top:1140px;height:290px;background:linear-gradient(180deg,var(--teal) 0%,var(--teal-dark) 100%);color:var(--white);text-align:center}
.relief h2{color:var(--white);padding-top:56px;font-size:30px}
.relief p{width:920px;margin:22px auto 28px;font-size:13px;line-height:1.7;opacity:.92}

/* team */
.team{top:1470px;height:420px}
.members{display:flex;justify-content:center;gap:60px;margin-top:50px}
.member{width:180px;text-align:center}
.portrait{width:170px;height:170px;border-radius:50%;margin:0 auto;border:5px solid var(--white);box-shadow:0 4px 12px rgba(0,0,0,.2)}
.member h4{font-family:"Raleway",sans-serif;color:var(--teal);font-size:16px;font-weight:600;margin-top:18px}
.member span{font-size:12px;color:var(--muted)}
.team-arrow{position:absolute;top:215px;font-size:40px;color:var(--muted)}

/* book band */
.book{top:1910px;height:300px;background:linear-gradient(90deg,var(--teal-dark),var(--teal));color:var(--white)}
.book-cover{position:absolute;left:290px;top:40px;width:200px;height:220px;background:linear-gradient(160deg,#f2f4f5 0%,#b8cdd4 55%,#5e8a99 100%);box-shadow:0 6px 14px rgba(0,0,0,.3)}
.book-text{position:absolute;left:550px;top:52px;width:380px}
.book-text h3{font-family:"Raleway",sans-serif;font-weight:400;font-size:30px}
.book-text h4{font-family:"Raleway",sans-serif;font-weight:400;font-size:19px;margin:12px 0 10px;line-height:1.35}
.book-text p{font-size:12px;line-height:1.6;opacity:.92;margin-bottom:16px}

/* cases */
.cases{top:2260px;height:290px}
.case-list{display:flex;justify-content:center;gap:110px;margin-top:38px}
.case{width:220px;text-align:center}
.case-img{width:100px;height:100px;border-radius:50%;margin:0 auto;background:radial-gradient(circle,#e86a4a 0%,#9c3f2f 45%,#2e3e5c 100%);box-shadow:0 3px 8px rgba(0,0,0,.2)}
.case h4{font-family:"Raleway",sans-serif;color:var(--teal);font-size:17px;font-weight:600;margin:14px 0 6px}
.case p{font-size:12px;line-height:1.6;color:var(--muted)}

/* contact */
.contact{top:2570px;height:260px;background:linear-gradient(180deg,var(--teal),var(--teal-dark));color:var(--white);text-align:center}
.contact h2{color:var(--white);padding-top:24px;font-size:30px}
.contact .intro{font-size:12px;margin:10px 0 14px;opacity:.92}
.form{display:flex;justify-content:center;gap:14px}
.fields{display:flex;flex-direction:column;gap:8px}
.field{width:240px;height:28px;background:var(--white);border-radius:2px;color:var(--muted);font-size:12px;text-align:left;padding:6px 10px}
.field.message{height:100px}
.submit{margin-top:14px}

/* affiliates */
.affiliates{top:2830px;height:110px;text-align:center}
.affiliates h3{font-family:"Raleway",sans-serif;font-weight:500;font-size:16px;color:var(--ink);padding-top:18px}
.badges{display:flex;justify-content:center;gap:40px;margin-top:14px}
.badge{width:130px;height:44px;border-radius:6px;background:var(--badge)}

/* footer */
.site-footer{top:2940px;height:108px;background:var(--soft);text-align:center;font-size:12px;color:var(--muted)}
.site-footer .addr{padding-top:30px}
.site-footer .addr a{color:var(--teal);text-decoration:none}
.site-footer .copy{margin-top:12px;font-size:11px}
</style>
</head>
<body>

<header class="site-header">
  <div class="brand"><span class="brand-dot"></span><span class="brand-name">Kelvale Heel Care</span></div>
  <div class="search">Find something...</div>
  <span class="book-now">Book Now</span>
  <div class="phone">
    <svg width="28" height="28" viewBox="0 0 28 28"><circle cx="14" cy="14" r="13" fill="var(--teal)"/><path d="M10 8l3 0 1 4-2 1a9 9 0 0 0 4 4l1-2 4 1 0 3c-6 1-12-5-11-11z" fill="#fff"/></svg>
    <div><small>CALL US</small><strong>(08) 5550 1428</strong></div>
  </div>
  <nav class="main-nav">
    <a class="current">Home</a><a>Common Problems</a><a>Services</a><a>About Us</a><a>Case Histories</a><a>Helpful Information</a><a>Blog</a><a>Contact</a>
  </nav>
</header>

<section class="hero">
  <div class="hero-photo" role="img" aria-label="Woman in sportswear seated on the ground holding her sore ankle, running shoes beside her"></div>
  <div class="hero-shade"></div>
  <h1 class="hero-title"><span class="l1">We offer</span><span class="l2">solutions to <b>Common</b><br><b>Foot</b> problems</span></h1>
  <div class="arrow left"></div><div class="arrow right"></div>
  <svg class="hero-wave" width="1200" height="90" viewBox="0 0 1200 90"><path d="M0 40 Q600 120 1200 40 L1200 90 L0 90Z" fill="var(--teal)"/><path d="M0 52 Q600 132 1200 52 L1200 90 L0 90Z" fill="#fff"/></svg>
</section>

<section class="practice">
  <h2>Practice Areas</h2><div class="rule"></div>
  <div class="cards">
    <div class="card"><div class="card-img" role="img" aria-label="Podiatrist examining a patient's foot" style="background:linear-gradient(135deg,#c7d9b4,#6f9a7a)"></div><h3>Common Problems</h3><p>Whether you suffer from a bone, joint or heel condition, our team can help you find a clear path to comfortable walking again.</p><span class="btn">Read More</span></div>
    <div class="card"><div class="card-img" role="img" aria-label="Foot being treated after surgery" style="background:linear-gradient(135deg,#f1d2c9,#c98c7e)"></div><h3>Foot &amp; Ankle Surgery</h3><p>Some problems are best treated with surgery. We explain every option simply so you can make a confident choice.</p><span class="btn">Read More</span></div>
    <div class="card"><div class="card-img" role="img" aria-label="Dancer's feet in ballet shoes" style="background:linear-gradient(135deg,#e6c3cc,#a56b7d)"></div><h3>Sport and Dance</h3><p>Active people place heavy loads on their feet. We treat sport and dance injuries and help you return safely.</p><span class="btn">Read More</span></div>
    <div class="card"><div class="card-img" role="img" aria-label="Clinic treatment room" style="background:linear-gradient(135deg,#d9e4ea,#7f9fb0)"></div><h3>All Our Services</h3><p>From routine nail care to custom orthotics, view the full list of services offered at our friendly clinic.</p><span class="btn">Read More</span></div>
  </div>
</section>

<section class="relief">
  <h2>Let Our Kelvale Podiatrists Relieve Your Foot and Ankle Pain</h2>
  <p>Whether you are an older adult, a sports person or a busy parent, foot and ankle pain can stop you doing the things you enjoy. Our experienced podiatrists take the time to listen, explain your condition in plain language and build a treatment plan that suits your lifestyle, so you can keep moving with comfort and confidence.</p>
  <span class="btn btn-light">Read More</span>
</section>

<section class="team">
  <h2>Meet Our Team</h2><div class="rule"></div>
  <span class="team-arrow" style="left:70px">&#8249;</span><span class="team-arrow" style="right:70px">&#8250;</span>
  <div class="members">
    <div class="member"><div class="portrait" role="img" aria-label="Portrait of podiatric surgeon" style="background:linear-gradient(180deg,#e8ecee,#9fb2bb)"></div><h4>Dr Owen Marl</h4><span>Podiatric Surgeon</span></div>
    <div class="member"><div class="portrait" role="img" aria-label="Portrait of podiatrist" style="background:linear-gradient(180deg,#e4e8ea,#7d93a3)"></div><h4>Graham Tilby</h4><span>Podiatrist</span></div>
    <div class="member"><div class="portrait" role="img" aria-label="Portrait of podiatrist" style="background:linear-gradient(180deg,#ece8e4,#a89482)"></div><h4>Nadia Fenwick</h4><span>Podiatrist</span></div>
    <div class="member"><div class="portrait" role="img" aria-label="Portrait of podiatrist" style="background:linear-gradient(180deg,#eee9e6,#b89d8c)"></div><h4>Dr Ruth Callow</h4><span>Podiatrist</span></div>
  </div>
</section>

<section class="book">
  <div class="book-cover" role="img" aria-label="Cover of the podiatric surgery book showing a surgical team"></div>
  <div class="book-text">
    <h3>Free Book</h3>
    <h4>Free Foot Surgery Book by Podiatric Surgeon, Dr Owen Marl</h4>
    <p>This book was created to help people understand common foot problems and when they might be helped by surgery. Request your copy today.</p>
    <span class="btn btn-light">Read More</span>
  </div>
</section>

<section class="cases">
  <h2>Case Histories</h2><div class="rule"></div>
  <div class="case-list">
    <div class="case"><div class="case-img" role="img" aria-label="Highlighted painful heel area"></div><h4>Plantar fasciitis Case</h4><p>Read how careful assessment and a simple treatment plan eased heel pain for a keen walker within weeks.</p></div>
    <div class="case"><div class="case-img" role="img" aria-label="Highlighted bunion on the big toe joint"></div><h4>Bunion Case</h4><p>A patient's story of bunion correction, from first visit to recovery and a return to everyday shoes.</p></div>
    <div class="case"><div class="case-img" role="img" aria-label="Highlighted injured ankle"></div><h4>Trauma case</h4><p>How our team guided an injured ankle through healing with clear advice at every step of the way.</p></div>
  </div>
</section>

<section class="contact">
  <h2>Contact Us</h2>
  <p class="intro">Please fill out the form below and someone will get back to you shortly.</p>
  <div class="form">
    <div class="fields"><div class="field">Name</div><div class="field">Email</div><div class="field">Phone</div></div>
    <div class="field message">Message</div>
  </div>
  <span class="btn btn-light submit">Submit now</span>
</section>

<section class="affiliates">
  <h3>Our Trusted Affiliates</h3>
  <div class="badges">
    <span class="badge"></span><span class="badge"></span><span class="badge"></span><span class="badge"></span><span class="badge"></span>
  </div>
</section>

<footer class="site-footer">
  <p class="addr">Kelvale Office: 12 Larch Street &nbsp;·&nbsp; Phone: (08) 5550 1428 &nbsp;·&nbsp; <a>Location Details</a> &nbsp;·&nbsp; <a>Get Directions</a></p>
  <p class="copy">© 2018 Kelvale Heel Care. All Rights Reserved | Privacy Policy</p>
</footer>

</body>
</html>
```